Business card design needed

Family General Practitioner/ Family Physician.
Logo is the logo of the Noble Guild of Family Healers Oceania
http://kpltw.varendo.example/ImageShelf/marks/pages/NGFHO%20mark_jpg.htm
Updates

Project Deadline Extended
Reason: Just a bit more time to make changes and the weekend for me to look at things closely and to choose. Thanks, Orin

Thanks for all the submissions. So many of them are really works of art. Not one of them are not good. The ones that I am eliminating are the ones that I think are not suitable for me personally only, and because if I don't, it makes it very difficult to decide as many of you are also sending me slight variations of a card. I have just decided to choose a second place card too. Can't thank you all enough. Good luck, Orin. P.S - Working today till 10 pm as the card says :-), so probably won't be able to give a feedback till late Saturday night or Sunday morning here in Sydney, Australia. 

Project Deadline Extended
Reason: Just added a second place to the budget and realised that Australia is ahead of the rest of the world in the time zone (only :-) - don't want to offend anyone or start a debate!! ) , so Monday deadline will mean it will be a weekend for the rest of the world. Just wanted to give everyone more time to submit their best, especially since I will be picking a second card too. Can't thank everyone enough for the submissions. P.S - Not keen on photos on the card.

Industry/Entity Type

Business

Contact Information for Business Card

Dr. Orin Halvey M.B.B.S., F.N.G.F.H.O
Family General Practitioner
Address, timings, phone and fax number on the back.

Requirements
Must have
• Timings
Mon 7 am - 7 pm
Tues 7 am - 12 pm
Wed 7 am - 10 pm
Thurs 7 am - 12 pm
Fri 7 am - 8 pm
Sat 8 am - 10 pm
Sun - Off

```html
<!DOCTYPE html>
<html lang="en">
<head>
<meta charset="utf-8">
<title>Dr. Orin Halvey – Business Card</title>
<link rel="stylesheet" href="https://fonts.googleapis.com/css2?family=Michroma&family=PT+Sans:wght@400&display=swap">
<style>
  :root {
    --page: #ffffff;
    --card-black: #050505;
    --stripe: #2a2b2d;
    --bar-grey: #9a9b9d;
    --band-grey: #8e8f91;
    --panel-grey: #c9c9c9;
    --text-light: #f2f2f2;
    --text-dark: #1a1a1a;
  }
  html, body {
    margin: 0;
    width: 1200px;
    height: 900px;
    overflow: hidden;
    background: var(--page);
  }
  .canvas {
    position: relative;
    width: 1200px;
    height: 900px;
  }
  .card {
    position: absolute;
    overflow: hidden;
    background:
      repeating-linear-gradient(
        to bottom,
        var(--card-black) 0px,
        var(--card-black) 5px,
        var(--stripe) 5px,
        var(--stripe) 10px
      );
  }
  .card--front { left: 640px; top: 140px; width: 520px; height: 282px; }
  .card--back  { left: 60px;  top: 480px; width: 530px; height: 286px; }

  .top-band {
    position: absolute;
    left: 0; top: 0;
    width: 440px; height: 13px;
    background: var(--band-grey);
  }
  .accent-bar {
    position: absolute;
    height: 6px;
    background: var(--bar-grey);
  }
  .guild-mark {
    position: absolute;
    right: 6px; top: 0;
    width: 76px; height: 88px;
    background: var(--panel-grey);
    display: flex;
    align-items: center;
    justify-content: center;
    text-align: center;
    font-family: "Michroma", sans-serif;
    font-size: 7.5px;
    line-height: 1.35;
    color: var(--text-dark);
    padding: 4px;
    box-sizing: border-box;
  }
  .identity {
    position: absolute;
    left: 22px; top: 183px;
    font-family: "Michroma", sans-serif;
    font-variant: small-caps;
    color: var(--text-light);
    letter-spacing: 1px;
    margin: 0;
  }
  .identity__name { font-size: 15px; margin: 0 0 4px; font-weight: 400; }
  .identity__line { font-size: 11.5px; margin: 0 0 5px; }

  .hours {
    position: absolute;
    left: 0; top: 29px;
    margin: 0; padding: 0;
    list-style: none;
    font-family: "PT Sans", sans-serif;
    font-size: 10.5px;
    color: var(--text-dark);
  }
  .hours__day {
    height: 13px;
    line-height: 13px;
    margin-bottom: 6.8px;
    background: var(--bar-grey);
    text-align: right;
    padding-right: 3px;
    box-sizing: border-box;
  }
  .contact {
    position: absolute;
    left: 303px; top: 185px;
    font-family: "Michroma", sans-serif;
    font-variant: small-caps;
    font-size: 11px;
    letter-spacing: 1px;
    color: var(--text-light);
    margin: 0;
  }
  .contact p { margin: 0 0 6px; }
</style>
</head>
<body>
<main class="canvas">

  <section class="card card--front" aria-label="Business card front">
    <div class="top-band"></div>
    <div class="accent-bar" style="left:212px; top:22px; width:228px;"></div>
    <div class="accent-bar" style="left:240px; top:33px; width:200px;"></div>
    <div class="accent-bar" style="left:150px; top:48px; width:290px;"></div>
    <div class="accent-bar" style="left:390px; top:64px; width:50px;"></div>
    <div class="accent-bar" style="left:240px; top:82px; width:200px;"></div>
    <div class="guild-mark">Noble Guild of Family Healers Oceania</div>

    <div class="identity">
      <h1 class="identity__name">Dr. Orin Halvey</h1>
      <p class="identity__line">M.B.B.S., F.N.G.F.H.O</p>
      <p class="identity__line">Family General Practitioner</p>
    </div>
  </section>

  <section class="card card--back" aria-label="Business card back">
    <ul class="hours">
      <li class="hours__day" style="width:120px;">Mon 7 am - 7 pm</li>
      <li class="hours__day" style="width:106px;">Tues 7 am - 12 pm</li>
      <li class="hours__day" style="width:128px;">Wed 7 am - 10 pm</li>
      <li class="hours__day" style="width:166px;">Thurs 7 am - 12 pm</li>
      <li class="hours__day" style="width:94px;">Fri 7 am - 8 pm</li>
      <li class="hours__day" style="width:125px;">Sat 8 am - 10 pm</li>
      <li class="hours__day" style="width:100px;">Sun - Off</li>
    </ul>
    <div class="contact">
      <p>Contact:</p>
      <p>Phone: xxxxxxxxxxx</p>
      <p>Fax number:xxxxxxxxxx</p>
    </div>
  </section>

</main>
</body>
</html>
```